Ridgeline Journeys business card

please see website
www.ridgelinejourneys.comau

info needed on card
Curtis Halvey
Ph
email
Adventure Riding GPS trails

please use my logo and colours off my site

Curtis Halvey
curtis@ridgelinejourneys.com

```html
<!DOCTYPE html>
<html lang="en">
<head>
<meta charset="utf-8">
<title>Ridgeline Journeys – Business Card</title>
<link rel="stylesheet" href="https://fonts.googleapis.com/css2?family=Arimo:wght@400;700&display=swap">
<style>
  :root {
    --page-bg: #d9d4cc;
    --card-white: #f4f4f4;
    --brand-yellow: #f2e33a;
    --brand-black: #0b0b0b;
    --ink: #1a1a1a;
    --contact-text: #dcdcdc;
    --name-text: #f2f2f2;
    --divider: #8a8a8a;
  }
  * { margin: 0; padding: 0; box-sizing: border-box; }
  html, body {
    width: 1200px;
    height: 902px;
    overflow: hidden;
    background: var(--page-bg);
    font-family: "Arimo", Arial, sans-serif;
  }
  .card {
    position: absolute;
    left: 60px;
    top: 142px;
    width: 1080px;
    height: 617px;
    background: var(--card-white);
    overflow: hidden;
    box-shadow: 0 10px 30px rgba(0,0,0,0.18);
  }
  .card__wave {
    position: absolute;
    inset: 0;
    width: 100%;
    height: 100%;
  }
  .brand {
    position: absolute;
    left: 150px;
    top: 150px;
    display: flex;
    align-items: center;
    gap: 34px;
  }
  .brand__dot {
    width: 120px;
    height: 120px;
    border-radius: 50%;
    background: var(--brand-yellow);
  }
  .brand__name {
    font-weight: 700;
    font-size: 62px;
    line-height: 1.05;
    color: var(--ink);
    text-transform: uppercase;
    letter-spacing: 1px;
  }
  .holder-name {
    position: absolute;
    left: 50px;
    bottom: 48px;
    font-size: 54px;
    color: var(--name-text);
  }
  .divider {
    position: absolute;
    left: 488px;
    top: 440px;
    width: 2px;
    height: 150px;
    background: var(--divider);
  }
  .contact {
    position: absolute;
    left: 512px;
    top: 452px;
    list-style: none;
  }
  .contact__item {
    display: flex;
    align-items: center;
    gap: 18px;
    height: 56px;
    font-size: 30px;
    color: var(--contact-text);
  }
  .contact__icon {
    width: 28px;
    height: 28px;
    flex: none;
  }
</style>
</head>
<body>
  <article class="card">
    <svg class="card__wave" viewBox="0 0 1080 617" preserveAspectRatio="none" aria-hidden="true">
      <path fill="var(--brand-yellow)" d="M0,392 C300,402 600,392 780,302 C900,242 1000,222 1080,217 L1080,617 L0,617 Z"/>
      <path fill="var(--brand-black)" d="M0,422 C300,432 600,422 790,332 C910,274 1000,256 1080,252 L1080,617 L0,617 Z"/>
    </svg>

    <div class="brand">
      <span class="brand__dot"></span>
      <h1 class="brand__name">Ridgeline<br>Journeys</h1>
    </div>

    <p class="holder-name">Curtis Halvey</p>
    <span class="divider"></span>

    <ul class="contact">
      <li class="contact__item">
        <svg class="contact__icon" viewBox="0 0 28 28" aria-hidden="true">
          <rect x="1" y="1" width="26" height="26" rx="3" fill="#e6e6e6"/>
          <path d="M8 7c1-1 2-1 3 0l2 3c.5 1 0 1.6-.6 2.2l-.8.8c1 2 2.4 3.4 4.4 4.4l.8-.8c.6-.6 1.2-1.1 2.2-.6l3 2c1 1 1 2 0 3l-1 1c-2 2-7 0-10-3S6 10 8 8z" fill="#111"/>
        </svg>
        <span>curtis@ridgelinejourneys.com</span>
      </li>
      <li class="contact__item">
        <svg class="contact__icon" viewBox="0 0 28 28" aria-hidden="true">
          <rect x="1" y="1" width="26" height="26" rx="3" fill="#e6e6e6"/>
          <circle cx="14" cy="14" r="9" fill="none" stroke="#111" stroke-width="2"/>
          <ellipse cx="14" cy="14" rx="4" ry="9" fill="none" stroke="#111" stroke-width="1.6"/>
          <line x1="5" y1="14" x2="23" y2="14" stroke="#111" stroke-width="1.6"/>
        </svg>
        <span>www.ridgelinejourneys.com.au</span>
      </li>
    </ul>
  </article>
</body>
</html>
```